Business Card for Polygraph business in Africa

Business Card . Polygraph Examiner based in Tanzania, East Africa.
Business Card will be used to disseminate contact information to potential clients.
It should convey that I am a professional specifically in the polygraph field and perform my work with integrity.

I have attached the business card that I'm currently using, which I threw together myself initially. It's not professional enough.

Target Market(s)

Banks, Accounting Firms, Government Ministries, Gas, Oil, & Gemstone Mining Concerns, Wildlife Conservation NGOs, International companies located in East Africa.

Industry/Entity Type

Business

Contact Information for Business Card

Veritrace Kilonga
Miriam Holloway
PO Box 48317
Arusha, Tanzania
+255 612 839 274
miriamholloway@postvale.example

Colors
00a990
f37122
faa54b

Requirements
Must have
• - Veritrace Kilonga (with the word "Polygraph" being more prominent than the word "Tanzania")
• - Forensic Examinations
• - Employment Screening
• - Should contain a logo of the Continental Truthline Society (of which I'm a member)
• - I would like an accent design (such as the polygraph "squiggles" of a cardio tracing or such as that)
• - My contact information (less prominent, but large enough to read legibly). I would also consider putting the contact information on the second side of the card.
Nice to have
• My color suggestions are changeable.
Should not have
• Anything "cutesy" or "cartoonish"

```html
<!DOCTYPE html>
<html lang="en">
<head>
<meta charset="utf-8">
<title>Veritrace Kilonga — Business Card</title>
<link rel="stylesheet" href="https://fonts.googleapis.com/css2?family=Open+Sans:wght@400;600;700&family=Cormorant+Garamond:wght@500;600&display=swap">
<style>
  :root {
    --backdrop: #3a3431;
    --card: #0d0d0d;
    --card-edge: #1c1c1c;
    --teal: #00a990;
    --orange: #f37122;
    --apricot: #faa54b;
    --ink: #f2f2f2;
    --silver: #c9c9c9;
    --silver-dim: #9a9a9a;
    --divider: #2c2c2c;
  }
  * { box-sizing: border-box; margin: 0; padding: 0; }
  html, body { width: 1200px; height: 900px; overflow: hidden; }
  body {
    background: var(--backdrop);
    font-family: "Open Sans", Arial, sans-serif;
    position: relative;
  }
  .card {
    position: absolute;
    top: 300px;
    width: 525px;
    height: 300px;
    background: var(--card);
    border: 1px solid var(--card-edge);
    box-shadow: 0 14px 30px rgba(0,0,0,.45);
  }
  .card--contact { left: 50px; }
  .card--brand { left: 625px; }

  /* contact side */
  .brand-panel {
    position: absolute; left: 0; top: 0; bottom: 0; width: 215px;
    display: flex; flex-direction: column; align-items: center; justify-content: center; gap: 16px;
  }
  .brand-dot {
    width: 120px; height: 120px; border-radius: 50%;
    background: var(--teal);
  }
  .brand-name {
    color: var(--ink); font-size: 17px; font-weight: 600; letter-spacing: .5px;
  }
  .panel-divider {
    position: absolute; left: 215px; top: 40px; bottom: 40px; width: 1px;
    background: var(--divider);
  }
  .contact {
    position: absolute; left: 250px; top: 58px; color: var(--ink);
  }
  .person-name { font-size: 21px; font-weight: 700; line-height: 1.1; }
  .person-name .first { color: var(--teal); }
  .person-name .last { color: var(--orange); }
  .person-role { font-size: 13.5px; margin-top: 4px; }
  .address { font-size: 14px; line-height: 1.45; margin-top: 30px; padding-left: 22px; }
  .reach { list-style: none; margin-top: 20px; font-size: 13.5px; line-height: 1.6; }
  .reach li { display: flex; align-items: center; gap: 10px; }
  .reach svg { width: 12px; height: 12px; flex: none; }

  /* brand side */
  .brand-face {
    position: absolute; inset: 0;
    display: flex; flex-direction: column; align-items: center; justify-content: center;
    font-family: "Cormorant Garamond", "Times New Roman", serif;
    color: var(--silver);
  }
  .brand-face .brand-dot {
    width: 110px; height: 110px;
    background: linear-gradient(145deg, #e6e6e6, #8d8d8d);
  }
  .brand-title {
    margin-top: 20px; font-size: 30px; font-weight: 600; letter-spacing: 2px;
    text-transform: uppercase; color: var(--silver);
    border-bottom: 1px solid var(--silver-dim); padding-bottom: 6px;
  }
  .services {
    list-style: none; margin-top: 16px; text-align: center;
    font-size: 15px; letter-spacing: 1.5px; text-transform: uppercase;
    color: var(--silver-dim); line-height: 1.5;
  }
</style>
</head>
<body>
  <section class="card card--contact">
    <div class="brand-panel">
      <div class="brand-dot"></div>
      <div class="brand-name">Veritrace Kilonga</div>
    </div>
    <div class="panel-divider"></div>
    <div class="contact">
      <h1 class="person-name"><span class="first">Miriam</span> <span class="last">Holloway</span></h1>
      <p class="person-role">Polygraph Examiner</p>
      <p class="address">PO Box 48317<br>Arusha, Tanzania</p>
      <ul class="reach">
        <li>
          <svg viewBox="0 0 12 12" aria-hidden="true"><path fill="#00a990" d="M2.4 0.6l2 2.2-1 1.3c.7 1.5 1.9 2.7 3.4 3.4l1.3-1 2.2 2-1.1 1.9C4.9 10 1.9 7 1 2.8z"/></svg>
          +255 612 839 274
        </li>
        <li>
          <svg viewBox="0 0 12 12" aria-hidden="true"><rect x="0.5" y="2" width="11" height="8" fill="#00a990"/><path d="M0.8 2.4L6 6.6l5.2-4.2" stroke="#0d0d0d" stroke-width="1.1" fill="none"/></svg>
          miriamholloway@postvale.example
        </li>
      </ul>
    </div>
  </section>

  <section class="card card--brand">
    <div class="brand-face">
      <div class="brand-dot"></div>
      <div class="brand-title">Veritrace Kilonga</div>
      <ul class="services">
        <li>Forensic Examinations</li>
        <li>Employment Screening</li>
      </ul>
    </div>
  </section>
</body>
</html>
```